Structural Engineering Business Card

Brookvane Drafting does residential house plans for clients in Central Florida. Would like simple but elegant business card that is appropriate for a house plan engineering company. Prefer black business card with black/white them but open to other shades of blue. I uploaded a sample card that I came across that looked good but please come up with your own creative designs.

Contact Information for Business Card

Name, Title, Phone, Email, Address, website

```html
<!DOCTYPE html>
<html lang="en">
<head>
<meta charset="utf-8">
<title>Brookvane Drafting – Business Card</title>
<link href="https://fonts.googleapis.com/css2?family=Arimo:wght@400;700&display=swap" rel="stylesheet">
<style>
  :root {
    --backdrop: #c8c8c8;
    --card: #1c1c1c;
    --ink: #ffffff;
    --ink-soft: #e4e4e4;
    --rule: #8a8a8a;
    --gloss: #0a0a0a;
  }
  * { box-sizing: border-box; margin: 0; padding: 0; }
  html, body { width: 1200px; height: 788px; overflow: hidden; }
  body {
    background: var(--backdrop);
    font-family: "Arimo", Arial, sans-serif;
    display: flex;
    align-items: center;
    justify-content: center;
    gap: 36px;
  }
  .card {
    position: relative;
    width: 540px;
    height: 310px;
    border-radius: 26px;
    background: var(--card);
    color: var(--ink);
    overflow: hidden;
  }
  .card-front .brand {
    position: absolute;
    left: 38px;
    top: 116px;
    display: flex;
    align-items: center;
    gap: 10px;
    font-size: 26px;
    font-weight: 700;
    letter-spacing: 0.5px;
    text-transform: uppercase;
    line-height: 1;
    white-space: nowrap;
  }
  .brand-dot {
    width: 14px; height: 14px; border-radius: 50%;
    background: var(--ink);
    flex: none;
  }
  .person {
    position: absolute;
    right: 38px;
    top: 48px;
    text-align: right;
    white-space: nowrap;
  }
  .person-name {
    font-size: 19px;
    font-weight: 700;
    letter-spacing: 1px;
    text-transform: uppercase;
    line-height: 1.1;
  }
  .person-title {
    font-size: 14px;
    color: var(--ink-soft);
    margin-top: 4px;
  }
  .divider {
    position: absolute;
    left: 38px;
    right: 38px;
    top: 168px;
    height: 1px;
    background: var(--rule);
  }
  .contacts {
    position: absolute;
    left: 38px;
    top: 190px;
    list-style: none;
    font-size: 14.5px;
    line-height: 1;
  }
  .contacts li {
    display: flex;
    align-items: center;
    gap: 8px;
    margin-bottom: 10px;
    white-space: nowrap;
  }
  .contacts svg { width: 12px; height: 12px; flex: none; }
  .address {
    position: absolute;
    right: 38px;
    top: 190px;
    text-align: right;
    font-size: 14.5px;
    line-height: 1.55;
    font-style: normal;
    white-space: nowrap;
  }
  .card-back {
    display: flex;
    align-items: center;
    justify-content: center;
    padding: 0 30px;
  }
  .card-back .brand-gloss {
    font-size: 36px;
    font-weight: 700;
    text-transform: uppercase;
    color: var(--gloss);
    letter-spacing: 0.5px;
    white-space: nowrap;
  }
</style>
</head>
<body>
  <section class="card card-front" aria-label="Card front">
    <div class="person">
      <div class="person-name">Daniel Whitford</div>
      <div class="person-title">Founder/CEO</div>
    </div>
    <div class="brand"><span class="brand-dot"></span>Brookvane Drafting</div>
    <div class="divider"></div>
    <ul class="contacts">
      <li>
        <svg viewBox="0 0 12 12" aria-hidden="true"><path fill="#fff" d="M2 1h2.2l1 2.6-1.3 1a6 6 0 0 0 3.5 3.5l1-1.3 2.6 1V10a1 1 0 0 1-1 1A9 9 0 0 1 1 2a1 1 0 0 1 1-1z"/></svg>
        555.014.2870
      </li>
      <li>
        <svg viewBox="0 0 12 12" aria-hidden="true"><rect x="0.5" y="2" width="11" height="8" rx="1" fill="#fff"/><path d="M1 2.6 6 6.5l5-3.9" fill="none" stroke="#1c1c1c" stroke-width="1"/></svg>
        info@brookvanedrafting.com
      </li>
      <li>
        <svg viewBox="0 0 12 12" aria-hidden="true"><circle cx="6" cy="6" r="5.2" fill="none" stroke="#fff" stroke-width="1.2"/><ellipse cx="6" cy="6" rx="2.2" ry="5.2" fill="none" stroke="#fff" stroke-width="1"/><path d="M1 6h10" stroke="#fff" stroke-width="1"/></svg>
        www.brookvanedrafting.com
      </li>
    </ul>
    <address class="address">
      1290 Harbor Blvd Suite 310<br>
      Lakeview, FL 32801
    </address>
  </section>

  <section class="card card-back" aria-label="Card back">
    <div class="brand-gloss">Brookvane Drafting</div>
  </section>
</body>
</html>
```